SkyvornQ Business Cards and Stationary Design

Need a design for our business cards and stationary. I want to carry on the theme of the logo. I want the business cards to have a design on the back. I would like the business cards and the stationary to carry the same theme, design scheme, and branding

Target Market(s)

Airlines and Maintenance Facilities

Industry/Entity Type

Aviation

Contact Information for Business Card

Name
Position Title
Address: 4827 Trellis Hollow Road, Fort Pierce, Florida, 34951
Office Number
Mobile Number
Email
Website

Font styles to use
Serif
Sans Serif

Colors

Designer to choose colors to be used in the design.

```html
<!DOCTYPE html>
<html lang="en">
<head>
<meta charset="utf-8">
<title>SkyvornQ Business Card</title>
<link rel="stylesheet" href="https://fonts.googleapis.com/css2?family=Open+Sans:wght@300;400;600;700&display=swap">
<style>
  :root {
    --backdrop: #d5d6d8;
    --charcoal: #231f20;
    --navy: #16284f;
    --navy-deep: #1b2a58;
    --sky: #2a9ad8;
    --sky-light: #3aa6e2;
    --back-edge: #21508d;
    --white: #ffffff;
  }
  html, body {
    margin: 0;
    padding: 0;
    width: 1200px;
    height: 1073px;
    overflow: hidden;
    background: radial-gradient(circle at 40% 30%, #eceded 0%, var(--backdrop) 80%);
    font-family: "Open Sans", sans-serif;
  }
  .canvas {
    position: relative;
    width: 1200px;
    height: 1073px;
  }
  .card {
    position: absolute;
    width: 826px;
    height: 471px;
    border-radius: 26px;
    overflow: hidden;
  }
  .card-front { left: 332px; top: 54px; background: var(--charcoal); }
  .card-back {
    left: 47px; top: 553px;
    background: radial-gradient(ellipse at 52% 42%, var(--sky-light) 0%, #2480c0 45%, var(--back-edge) 100%);
  }
  .front-art { position: absolute; inset: 0; width: 100%; height: 100%; }

  .brand {
    position: absolute;
    left: 0; top: 30px;
    width: 448px;
    text-align: center;
  }
  .brand-mark {
    display: block;
    width: 110px; height: 110px;
    margin: 0 auto 16px;
    border: 9px solid var(--sky);
    border-radius: 50%;
    box-sizing: border-box;
  }
  .brand-name {
    color: var(--navy-deep);
    font-weight: 700;
    font-size: 40px;
    letter-spacing: 5px;
    line-height: 1;
  }

  .person {
    position: absolute;
    right: 31px; top: 37px;
    text-align: right;
    color: var(--white);
  }
  .person-name { font-weight: 700; font-size: 26px; letter-spacing: 0.5px; line-height: 1.25; }
  .person-title { font-weight: 300; font-size: 23px; letter-spacing: 0.5px; line-height: 1.25; }

  .contact-list {
    position: absolute;
    right: 31px; top: 315px;
    margin: 0; padding: 0;
    list-style: none;
    color: var(--white);
    font-size: 18px;
  }
  .contact-list li {
    display: flex;
    justify-content: flex-end;
    align-items: center;
    gap: 6px;
    height: 34px;
  }
  .icon { width: 17px; height: 17px; flex: none; }

  .address {
    position: absolute;
    left: 42px; top: 390px;
    display: flex;
    gap: 8px;
    color: var(--white);
    font-size: 18px;
    line-height: 30px;
  }
  .address .icon { margin-top: 6px; }

  .back-mark {
    position: absolute;
    left: 290px; top: 62px;
    width: 272px; height: 272px;
    border: 14px solid var(--navy-deep);
    border-radius: 50%;
    box-sizing: border-box;
    display: flex;
    align-items: center;
    justify-content: center;
  }
  .back-name {
    color: var(--white);
    font-weight: 700;
    font-size: 36px;
    letter-spacing: 3px;
  }
  .back-url {
    position: absolute;
    left: 0; right: 0; top: 378px;
    text-align: center;
    color: var(--white);
    font-size: 25px;
    letter-spacing: 5px;
    padding-right: 40px;
  }
</style>
</head>
<body>
<main class="canvas">
  <section class="card card-front" aria-label="Business card front">
    <svg class="front-art" viewBox="0 0 759 433" preserveAspectRatio="none" aria-hidden="true">
      <path d="M0,215 C130,318 280,330 420,306 C540,286 630,232 759,228 V433 H0 Z" fill="var(--navy)"/>
      <path d="M0,222 C130,322 280,336 420,312 C540,292 630,240 759,236" fill="none" stroke="var(--sky)" stroke-width="3"/>
      <path d="M0,232 C130,332 280,344 420,320 C540,300 630,252 759,248" fill="none" stroke="var(--sky)" stroke-width="2"/>
      <path d="M0,0 H458 C492,70 484,205 380,266 C300,310 130,305 0,208 Z" fill="none" stroke="var(--sky)" stroke-width="3" transform="translate(6,4)"/>
      <path d="M0,0 H452 C488,70 478,200 376,260 C296,304 130,300 0,204 Z" fill="var(--white)" stroke="var(--navy)" stroke-width="1.5"/>
    </svg>

    <div class="brand">
      <span class="brand-mark" aria-hidden="true"></span>
      <div class="brand-name">SKYVORNQ</div>
    </div>

    <div class="person">
      <div class="person-name">DANIEL KORWICK</div>
      <div class="person-title">PRESIDENT</div>
    </div>

    <ul class="contact-list">
      <li>
        <svg class="icon" viewBox="0 0 20 20" aria-hidden="true"><circle cx="10" cy="10" r="8.5" fill="none" stroke="#fff" stroke-width="1.6"/><path d="M6.5,5.5 l2,0 1,2.5 -1.2,1 a6,6 0 0 0 2.7,2.7 l1,-1.2 2.5,1 0,2 a1,1 0 0 1 -1,1 a8,8 0 0 1 -8,-8 a1,1 0 0 1 1,-1z" fill="#fff"/></svg>
        <span>772-418-3056</span>
      </li>
      <li>
        <svg class="icon" viewBox="0 0 20 20" aria-hidden="true"><circle cx="10" cy="10" r="8.5" fill="none" stroke="#fff" stroke-width="1.6"/><rect x="7" y="5" width="6" height="10" rx="1" fill="none" stroke="#fff" stroke-width="1.4"/></svg>
        <span>772-904-2613</span>
      </li>
      <li>
        <svg class="icon" viewBox="0 0 20 20" aria-hidden="true"><circle cx="10" cy="10" r="8.5" fill="none" stroke="#fff" stroke-width="1.6"/><rect x="5.5" y="7" width="9" height="6.5" fill="none" stroke="#fff" stroke-width="1.3"/><path d="M5.5,7 L10,11 14.5,7" fill="none" stroke="#fff" stroke-width="1.3"/></svg>
        <span>info@skyvornq.com</span>
      </li>
      <li>
        <svg class="icon" viewBox="0 0 20 20" aria-hidden="true"><circle cx="10" cy="10" r="8.5" fill="none" stroke="#fff" stroke-width="1.6"/><ellipse cx="10" cy="10" rx="3.5" ry="8.5" fill="none" stroke="#fff" stroke-width="1.3"/><path d="M1.5,10 H18.5 M3,6 H17 M3,14 H17" stroke="#fff" stroke-width="1.2"/></svg>
        <span>www.skyvornq.com</span>
      </li>
    </ul>

    <div class="address">
      <svg class="icon" viewBox="0 0 20 20" aria-hidden="true"><circle cx="10" cy="10" r="8.5" fill="none" stroke="#fff" stroke-width="1.6"/><path d="M10,15 C7,11 6.5,9.5 6.5,8.5 a3.5,3.5 0 0 1 7,0 c0,1 -0.5,2.5 -3.5,6.5z" fill="none" stroke="#fff" stroke-width="1.3"/><circle cx="10" cy="8.5" r="1.2" fill="#fff"/></svg>
      <div>4827 Trellis Hollow Road, Fort Pierce,<br>Florida, 34951</div>
    </div>
  </section>

  <section class="card card-back" aria-label="Business card back">
    <div class="back-mark">
      <span class="back-name">SKYVORNQ</span>
    </div>
    <div class="back-url">www.skyvornq.com</div>
  </section>
</main>
</body>
</html>
```